Business card design

We need a business card designed completed for a new company. We are a company that works with associations, schools to convert their older text/DVDs into dynamic online and mobile programs. Our initial platform is designed for the legal associations and will enable their lawyers to access their content such as forms, videos, case law and support materials anywhere, anytime. We are also focused on Project Management Associations, Financial Management Associations and IT Associations.

I would like for the business card to have the following information:

Logo

Kent marrowby

President and CEO

kmarrowby@trevantiq.example

Mobile: 555-374-9160

www.trevantiq.example

Tag line: Transforming content into a mobile platform    

I would like it to be double sided, use the colours of the logo, tie into the mobile world

 

Industry/Entity Type

Legal

Logo Text

Trevantiq

```html
<!DOCTYPE html>
<html lang="en">
<head>
<meta charset="utf-8">
<title>Trevantiq business card</title>
<link rel="stylesheet" href="https://fonts.googleapis.com/css2?family=Source+Sans+3:ital,wght@0,400;0,700;1,700&display=swap">
<style>
  :root {
    --stage: #e8e5e1;
    --label: #2a2a2a;
    --card-grey: #8f8f8f;
    --card-white: #ffffff;
    --band-dark: #636363;
    --band-mid: #8c8c8c;
    --ink-dark: #3c3c3c;
    --ink-light: #ffffff;
    --logo-on-white: #5a5a5a;
  }
  * { box-sizing: border-box; margin: 0; padding: 0; }
  html, body { width: 1200px; height: 800px; overflow: hidden; }
  body {
    position: relative;
    background: var(--stage);
    font-family: "Source Sans 3", sans-serif;
  }
  .side-label {
    position: absolute;
    width: 300px;
    text-align: center;
    font-size: 22px;
    color: var(--label);
  }
  .card {
    position: absolute;
    width: 510px;
    height: 290px;
    border-radius: 20px;
    overflow: hidden;
    box-shadow: 0 4px 14px rgba(0,0,0,0.25);
  }
  .card--grey { background: var(--card-grey); color: var(--ink-light); }
  .card--white { background: var(--card-white); color: var(--ink-dark); }

  .tagline {
    position: absolute; top: 20px; width: 100%;
    text-align: center; font-size: 16px;
  }
  .logo-name {
    position: absolute; width: 100%; text-align: center;
    font-weight: 700; letter-spacing: 0.5px; line-height: 1;
  }
  .card--grey .logo-name { color: var(--ink-light); }
  .card--white .logo-name { color: var(--logo-on-white); }
  .logo-name--small { top: 103px; font-size: 58px; }
  .logo-name--large { top: 104px; font-size: 84px; }

  .holder {
    position: absolute; top: 203px; width: 100%;
    text-align: center; font-size: 18px;
  }
  .holder .role { font-size: 14px; }
  .phone {
    position: absolute; top: 232px; width: 100%;
    text-align: center; font-size: 13px; letter-spacing: 0.3px;
  }
  .phone b { font-style: italic; font-weight: 700; }

  .contact-band { position: absolute; left: 0; bottom: 0; width: 100%; height: 33px; }
  .band-part {
    position: absolute; top: 0; height: 33px;
    font-size: 14px; line-height: 33px;
  }
  .band-part--web { left: 0; width: 250px; clip-path: polygon(0 0, 230px 0, 250px 100%, 0 100%); padding-left: 43px; }
  .band-part--mail { right: 0; width: 280px; clip-path: polygon(0 0, 100% 0, 100% 100%, 20px 100%); text-align: center; padding-left: 24px; color: var(--ink-light); background: var(--band-dark); }
  .card--grey .band-part--web { background: var(--card-white); color: var(--ink-dark); }
  .card--white .band-part--web { background: var(--band-mid); color: var(--ink-dark); }

  .web-spaced {
    position: absolute; top: 254px; width: 100%;
    text-align: center; font-size: 16px; letter-spacing: 3px;
  }
  .card--grey .web-spaced { color: var(--ink-dark); }
</style>
</head>
<body>

  <div class="side-label" style="left:180px; top:50px;">Front</div>
  <div class="side-label" style="left:737px; top:50px;">Back - 1</div>
  <div class="side-label" style="left:180px; top:410px;">Back - 2</div>
  <div class="side-label" style="left:737px; top:410px;">Back - 3</div>

  <section class="card card--grey" style="left:80px; top:97px;">
    <p class="tagline">Transforming content into a mobile platform</p>
    <p class="logo-name logo-name--small">Trevantiq</p>
    <p class="holder">Kent marrowby, <span class="role">President and CEO</span></p>
    <p class="phone"><b>c</b> : 555-374-9160</p>
    <div class="contact-band">
      <div class="band-part band-part--web">www.trevantiq.example</div>
      <div class="band-part band-part--mail">kmarrowby@trevantiq.example</div>
    </div>
  </section>

  <section class="card card--white" style="left:629px; top:97px;">
    <p class="tagline">Transforming content into a mobile platform</p>
    <p class="logo-name logo-name--small">Trevantiq</p>
    <p class="holder">Kent marrowby, <span class="role">President and CEO</span></p>
    <p class="phone"><b>c</b> : 555-374-9160</p>
    <div class="contact-band">
      <div class="band-part band-part--web">www.trevantiq.example</div>
      <div class="band-part band-part--mail">kmarrowby@trevantiq.example</div>
    </div>
  </section>

  <section class="card card--grey" style="left:73px; top:452px;">
    <p class="logo-name logo-name--large">Trevantiq</p>
    <p class="web-spaced">www.trevantiq.example</p>
  </section>

  <section class="card card--white" style="left:633px; top:450px;">
    <p class="logo-name logo-name--large">Trevantiq</p>
    <p class="web-spaced">www.trevantiq.example</p>
  </section>

</body>
</html>
```